Electrician Business Card/ company logo/small business

New Business Cards and logo needed that will catch peoples eye and say we went that extra step. Attached is a design possibly to be incorporated, if u have your own great, lets see it!... This will be a small local business. thank you for all you do!
Halvern Electric
Ned Fosky Owner
Journeyman Electrician
phone 1.555.208.3471
email: KQLHalvernElectric@quellmail.net
call for free estimate!
Updates

Accepted and approved for cards

Target Market(s)

support small local business

Industry/Entity Type

Electrical,

Contact Information for Business Card

name, title,company/ logo, phone, email, free estimate

Other font styles liked:
• easy to read

Colors

Designer to choose colors to be used in the design.

Requirements
Must have
• eye catching everything! logo and halvern electric listed on business card/logo, incorp logo in the background of card
Nice to have
• lightening bolts in eyes or around the triangle? vertical, modern, any design that would be unique and stand out
Should not have
• pinks, reds, yellows,brown

```html
<!DOCTYPE html>
<html lang="en">
<head>
<meta charset="utf-8">
<title>Halvern Electric – Business Card</title>
<link rel="stylesheet" href="https://fonts.googleapis.com/css2?family=Open+Sans:wght@300;400;700&display=swap">
<style>
  :root {
    --stage: #1f2a2b;
    --card-dark: #2d2d2e;
    --card-light: #dcedf2;
    --cyan-top: #63d8f0;
    --cyan-bottom: #2bc3ea;
    --lime: #8dc63f;
    --ink: #1b1d1f;
    --blue: #2a8fd8;
    --white: #ffffff;
  }
  * { box-sizing: border-box; margin: 0; padding: 0; }
  html, body {
    width: 1200px; height: 861px; overflow: hidden;
    background: var(--stage);
    font-family: "Open Sans", Arial, sans-serif;
  }
  .cards {
    position: absolute; left: 60px; top: 282px;
    display: flex; gap: 40px;
  }
  .card {
    position: relative; width: 520px; height: 297px;
    border-radius: 22px; overflow: hidden;
  }
  /* Front */
  .card--front {
    background: var(--card-dark);
    display: flex; align-items: center; justify-content: center; gap: 12px;
  }
  .brand-square {
    width: 14px; height: 14px; background: var(--white);
  }
  .brand-name {
    color: var(--white); font-weight: 400; font-size: 26px; letter-spacing: 0.5px;
  }
  /* Back */
  .card--back { background: var(--card-light); }
  .side-band {
    position: absolute; left: 0; top: 0; bottom: 0; width: 140px;
    background: linear-gradient(180deg, var(--cyan-top), var(--cyan-bottom));
    display: flex; flex-direction: column; justify-content: flex-end;
    padding: 0 14px 34px;
  }
  .side-band .brand-name {
    font-size: 14px; font-weight: 300;
  }
  .accent-edge {
    position: absolute; right: 0; top: 0; width: 52px; height: 190px;
    background: var(--lime);
    border-bottom-left-radius: 40px;
  }
  .holder {
    position: absolute; left: 166px; top: 78px;
  }
  .holder-name {
    color: var(--ink); font-weight: 700; font-size: 20px;
  }
  .holder-role {
    color: var(--blue); font-weight: 300; font-size: 13px; margin-top: 1px;
  }
  .contact {
    position: absolute; left: 166px; top: 206px;
    list-style: none; font-size: 12px; color: var(--ink); font-weight: 300;
  }
  .contact li { line-height: 20px; }
  .contact .label {
    display: inline-block; width: 16px; color: var(--cyan-bottom); font-weight: 700;
  }
</style>
</head>
<body>
  <main class="cards">
    <section class="card card--front" aria-label="Card front">
      <span class="brand-square"></span>
      <span class="brand-name">Halvern Electric</span>
    </section>

    <section class="card card--back" aria-label="Card back">
      <div class="side-band">
        <span class="brand-name">Halvern Electric</span>
      </div>
      <div class="accent-edge"></div>
      <div class="holder">
        <h1 class="holder-name">Ned Fosky Journeyman</h1>
        <p class="holder-role">electrician</p>
      </div>
      <ul class="contact">
        <li><span class="label">P</span>1.555.208.3471</li>
        <li><span class="label">E</span>KQLHalvernElectric@quellmail.net</li>
      </ul>
    </section>
  </main>
</body>
</html>
```